Web design for new streaming audio service

We need a homepage design for a new streaming audio service. Our company is called Dunmoral, and we’re basically Vexlo for Audiobooks, Stand-Up Comedy, Lectures, Language Learning, etc. Essentially like Plumtrek for everything audio EXCEPT music.
You don’t have to code the homepage (Design Only), but it should include 3 different designs to work with 1) Web; 2) Phones; 3) Tablets.
Below is a link to a mockup of the web version which gives a good idea of what elements we want. This is just a mockup and we want you to improve it.
Once you download the mockup, please refer to the more detailed instructions below:
The following outlines the design project for the Dunmoral homepage. We have provided a rough mockup of the homepage layout that gives you a general idea of what we’re going for. There are a few elements that we are attached to, and many others where you have complete creative freedom to do whatever you think looks good.
The ZIP file includes the following:
* Mockup to see what we have in mind (dunmoral-homepage-mockup.jpg)
* Text used (dunmoral-homepage-text.txt)
* Raw image of actor (dunmoral-actor1.jpg)
* Raw images for samples (dunmoral-sample-[name].jpg)
Although we have only provided a mockup layout for the web version, we also need you to provide a mobile phone and a tablet version of the design also. It’s very possible the tablet version may be substantially similar to the web version, but the mobile phone version will likely be much different.
All of the raw files are included in the attached ZIP file. Please use our photographs and text as provided although cropping, sizing, etc. is flexible per the instructions below.
Display Requirements:
* Web Version - Minimum resolution 1024x768 (72 dpi) but should look good on 1920x1080 (72 dpi) - Page should be designed to scale to look acceptable in all resolutions in between.
* Phone Version - Minimum Zarno 4 - 640x960 (326 dpi) but should look good on Harlow Quasar T5 - 1920x1080 (441 dpi) - Page should be designed to scale to look acceptable in all resolutions and devices in between.
* Tablet Version - Minimum Bristly Ember QX 7” - 1280x800 (216 dpi) but should also look good on a Tavo Breeze - 2048x1536 (264 dpi) - Page should be designed to scale to look acceptable in all resolutions and devices in between.
Above the Fold - We want to make sure the Dunmoral logo, Member Login Link, Large Photo, Headline, Price, Button, and the first row of sample images are all “Above the fold”. As a general guideline, this means 600 pixels high on a 1024x768 72 dpi web screen. This requirement is less important on Phone versions.
Top Logo Bar - We want to retain the blue bar with the Dunmoral logo on the page, although we are open to a different size, shape and positioning if it greatly enhances the design. Please use the standard logo color, although you are welcome to use either the horizontal or vertical orientation of the logo based on your design.
Text color, font and size - Feel free to design the text in anyway you choose as long as the text is readable on the target platforms.
Buttons - Feel free to use any size, shape and colors for the buttons as long as they are obvious and clickable relative to the page. The only exception is the Chatterly button should follow the Chatterly color scheme and logo treatment (the mockup doesn’t seem 100% correct.)
Top Photograph - We want to retain the large photograph across the top of the screen although final shape and dimensions are flexible.
Size and shape of content samples (i.e. Audiobooks, Stand-Up Comedy, etc.) - Feel free to design the content samples in anyway you choose.
Three Sales Points (i.e. Listen on your Zarno…, All you can enjoy…, etc.) - The Three Sales Points are envisioned to each have a corresponding illustration which you should provide and have rights for. The placeholder is represented by a square next to the text. The color size and shape of these elements are flexible and can be designed in any way you choose.
Opt-in form - Feel free to design the opt-in form in anyway you choose as long as the text is readable and the interactivity is obvious on the target platforms.
Text links and copyright notice - Feel free to design the bottom of the page text links and copyright notice in anyway you choose.
Additional colors, graphic design elements, etc. - Feel free to use any additional colors, graphic design elements, etc. to support your design.
people who want to listen to audio through their mobile devices.
Graphic Design

```html
<!DOCTYPE html>
<html lang="en">
<head>
<meta charset="utf-8">
<title>Dunmoral – Unlimited Listening</title>
<link rel="stylesheet" href="https://fonts.googleapis.com/css2?family=Nunito+Sans:wght@300;400;600;700;800&display=swap">
<style>
:root{
  --brand-blue:#4a9cc9;
  --ink-blue:#1a5e8a;
  --title-blue:#1f6c98;
  --orange:#f7941d;
  --red:#e0262b;
  --paper:#eeeeee;
  --charcoal:#3d3d3d;
  --text:#555555;
  --muted:#cfcfcf;
  --chatterly:#3b5998;
  --white:#ffffff;
}
*{box-sizing:border-box;margin:0;padding:0}
html,body{width:1200px;height:2166px;overflow:hidden}
body{font-family:"Nunito Sans",Arial,sans-serif;color:var(--text);background:var(--paper);position:relative}
.abs{position:absolute}

/* header */
.site-header{position:absolute;left:0;top:0;width:1200px;height:81px;background:var(--brand-blue)}
.brand{position:absolute;left:101px;top:18px;display:flex;align-items:center;gap:12px;color:var(--white);font-weight:700;font-size:31px}
.brand-dot{width:40px;height:40px;border-radius:50%;background:var(--white)}
.login-btn{position:absolute;left:985px;top:22px;width:113px;height:37px;background:var(--orange);color:var(--white);border-radius:3px;font-size:17px;font-weight:600;display:flex;align-items:center;justify-content:center}

/* hero */
.hero{position:absolute;left:0;top:81px;width:1200px;height:564px;overflow:hidden}
.hero-photo{position:absolute;inset:0;background:linear-gradient(90deg,#f4f6f8 0%,#eef0f1 30%,#d9c2ad 55%,#a88468 72%,#5d6f86 100%)}
.hero-copy{position:absolute;left:108px;top:64px}
.hero-title{color:var(--ink-blue);font-size:34px;font-weight:800;line-height:1.2}
.hero-sub{color:var(--ink-blue);font-size:34px;font-weight:400;line-height:1.2}
.hero-price{margin-top:12px;color:#333;font-size:21px}
.hero-price strong{font-size:30px;font-weight:400}
.hero-arrow{position:absolute;left:395px;top:125px}
.email-input{background:var(--white);border:1px solid #cccccc;color:#999;font-size:13px;display:flex;align-items:center;padding-left:14px}
.cta-btn{background:var(--orange);color:var(--white);font-weight:700;display:flex;align-items:center;justify-content:center;border-radius:2px}
.note{color:var(--red);font-size:16px;font-weight:600}

/* section titles */
.section-title{position:absolute;left:118px;width:960px;display:flex;align-items:center;gap:22px;color:var(--title-blue);font-size:28px;font-weight:600;white-space:nowrap}
.section-title::before,.section-title::after{content:"";flex:1;height:1px;background:var(--muted)}

/* samples */
.sample{position:absolute;width:260px;text-align:center;font-size:16px;font-weight:600;color:#444}
.sample-art{width:156px;height:156px;border-radius:50%;margin:0 auto 20px}

/* features */
.features{position:absolute;left:0;top:1304px;width:1200px;height:227px;background:var(--charcoal)}
.feature{position:absolute;top:72px;display:flex;gap:16px}
.feature-icon{width:81px;height:81px;border-radius:50%;background:var(--brand-blue);display:flex;align-items:center;justify-content:center;flex:none}
.feature h3{color:var(--white);font-size:20px;font-weight:600;margin-top:8px}
.feature p{color:#cfcfcf;font-size:15px;line-height:1.5;margin-top:8px;width:220px}

/* trial */
.trial-copy{position:absolute;left:200px;top:1656px;width:800px;text-align:center;font-size:16px;line-height:29px;color:#555}
.or-divider{position:absolute;left:560px;top:1816px;width:80px;text-align:center;color:#999;font-size:17px}
.social-btn{position:absolute;left:481px;top:1863px;width:232px;height:43px;background:var(--chatterly);border:1px solid #2d4373;border-radius:3px;color:var(--white);font-size:16px;display:flex;align-items:center;gap:16px;padding-left:20px}
.social-square{width:16px;height:16px;background:var(--white);border-radius:2px}
.crowd{position:absolute;left:0;top:1978px;width:1200px;height:116px;background:linear-gradient(180deg,rgba(200,200,200,0) 0%,#c9c9c9 55%,#bdbdbd 100%)}

/* footer */
.site-footer{position:absolute;left:0;top:2094px;width:1200px;height:72px;background:var(--charcoal);color:#ddd;font-size:12.5px}
.footer-links{position:absolute;left:118px;top:27px;display:flex;gap:10px}
.footer-links span.sep{color:#888}
.copyright{position:absolute;right:101px;top:27px}
</style>
</head>
<body>

<header class="site-header">
  <div class="brand"><span class="brand-dot"></span>Dunmoral</div>
  <div class="login-btn">Log In</div>
</header>

<section class="hero">
  <div class="hero-photo" role="img" aria-label="Smiling young man wearing headphones looking at his phone"></div>
  <div class="hero-copy">
    <h1 class="hero-title">Unlimited Listening!</h1>
    <p class="hero-sub">Where ever you are</p>
    <p class="hero-price">Only <strong>$9.99</strong> Per Month</p>
  </div>
  <svg class="hero-arrow" width="60" height="110" viewBox="0 0 60 110" aria-hidden="true">
    <path d="M40 4 C60 40 50 80 8 102" fill="none" stroke="#f7a14a" stroke-width="2"/>
    <path d="M8 102 L20 92 M8 102 L22 104" fill="none" stroke="#f7a14a" stroke-width="2"/>
  </svg>
  <div class="email-input abs" style="left:108px;top:211px;width:273px;height:43px">Your email Address</div>
  <div class="cta-btn abs" style="left:108px;top:271px;width:273px;height:49px;font-size:18px">Start Your Free Trail</div>
  <p class="note abs" style="left:108px;top:334px">*Credit card not required</p>
</section>

<h2 class="section-title" style="top:700px">A sample of what you can listen to on Dunmoral</h2>

<div class="sample" style="left:69px;top:799px"><div class="sample-art" role="img" aria-label="Audiobook cover art" style="background:radial-gradient(circle,#5a6f74,#1c2a30)"></div>Audio Books</div>
<div class="sample" style="left:334px;top:799px"><div class="sample-art" role="img" aria-label="Stand-up comedy cover art" style="background:radial-gradient(circle,#b58c7a,#4b4a52)"></div>Stand-Up Comedy</div>
<div class="sample" style="left:599px;top:799px"><div class="sample-art" role="img" aria-label="Language learning cover art" style="background:radial-gradient(circle,#2a9ee0,#0b6fb8)"></div>Language Learning</div>
<div class="sample" style="left:865px;top:799px"><div class="sample-art" role="img" aria-label="Biography cover art" style="background:radial-gradient(circle,#d6d2c2,#8aa36a)"></div>Biographies &amp; Memory</div>

<div class="sample" style="left:69px;top:1038px"><div class="sample-art" role="img" aria-label="Guided meditation cover art" style="background:linear-gradient(180deg,#c55aa8,#7a3a9a)"></div>Guided Mediation</div>
<div class="sample" style="left:334px;top:1038px"><div class="sample-art" role="img" aria-label="Business training cover art" style="background:radial-gradient(circle,#8a5a2a,#2a1a12)"></div>Business Training</div>
<div class="sample" style="left:599px;top:1038px"><div class="sample-art" role="img" aria-label="Celebrity interview cover art" style="background:radial-gradient(circle,#e07aa0,#6a3048)"></div>Celebrities Interviews</div>
<div class="sample" style="left:865px;top:1038px"><div class="sample-art" role="img" aria-label="Fitness program cover art" style="background:radial-gradient(circle,#8fd0ea,#2a8ac0)"></div>Fitness Program</div>

<section class="features">
  <div class="feature" style="left:115px">
    <div class="feature-icon">
      <svg width="44" height="50" viewBox="0 0 44 50" aria-hidden="true">
        <rect x="4" y="2" width="28" height="44" rx="4" fill="none" stroke="#fff" stroke-width="3"/>
        <rect x="24" y="18" width="16" height="28" rx="3" fill="#4a9cc9" stroke="#fff" stroke-width="3"/>
        <circle cx="32" cy="41" r="1.8" fill="#fff"/>
      </svg>
    </div>
    <div><h3>Listen Anywhere</h3><p>Listen on your Zarno, Tavo or any Kestrel devices</p></div>
  </div>
  <div class="feature" style="left:475px">
    <div class="feature-icon"><span style="color:#fff;font-size:42px;font-weight:800">$</span></div>
    <div><h3>Low Pricing</h3><p>All you can enjoy for low monthly Price</p></div>
  </div>
  <div class="feature" style="left:805px">
    <div class="feature-icon">
      <svg width="34" height="34" viewBox="0 0 34 34" aria-hidden="true"><path d="M5 5 L29 29 M29 5 L5 29" stroke="#fff" stroke-width="4.5" stroke-linecap="round"/></svg>
    </div>
    <div><h3>No Obligation</h3><p>No Obligation cancel at anytime</p></div>
  </div>
</section>

<h2 class="section-title" style="top:1590px">Start your free Trial, No Risk</h2>
<p class="trial-copy">You will get instant &amp; unlimited access to all the material on Dunmoral for 14 days. There is no obligation &amp; you can cancel at anytime.</p>
<div class="email-input abs" style="left:274px;top:1743px;width:324px;height:49px">Your email Address</div>
<div class="cta-btn abs" style="left:619px;top:1743px;width:239px;height:49px;font-size:19px">Get Instant Access</div>
<div class="or-divider">— Or —</div>
<div class="social-btn"><span class="social-square"></span>Sign in with Chatterly</div>
<p class="note abs" style="left:0;width:1200px;text-align:center;top:1920px">*Credit card not required</p>
<div class="crowd" role="img" aria-label="Silhouette of a cheering crowd"></div>

<footer class="site-footer">
  <nav class="footer-links">
    <span>About</span><span class="sep">|</span><span>Help</span><span class="sep">|</span><span>Contact Us</span><span class="sep">|</span><span>Member Login</span><span class="sep">|</span><span>Privacy Policy</span><span class="sep">|</span><span>Terms of Service</span>
  </nav>
  <div class="copyright">© 2014 Dunmoral LLC - All Rights Reserved</div>
</footer>

</body>
</html>
```